Mortgage Specialist Wordpress Build

I have a current WordPress site but I would like a whole new site built using the same domain. I've included a site for reference in my outline. The main focus of the website is to educate and capture leads.
I would like my blogs to stay for SEO already earned. Please see work requested attached.
Updates
Project Deadline Extended Reason: I am extending the deadline because I didn't realize this was a design only and I need the website coded as well. I've purchased the add-on. This is my first time using Pixel Harbor so please bare with me. I have additional Wordpress sites I want to have built too. Thanks, Colin Added Tuesday, April 18, 2017
Target Market(s)
Home Buyers, Home owners looking to refinance or renew their mortgages
Industry/Entity Type
Mortgage
Coding
Coded - Design and coding required
Font styles to use
Look and feel
Each slider illustrates characteristics of the customer's brand and the style your logo design should communicate.

```html
<!DOCTYPE html>
<html lang="en">
<head>
<meta charset="utf-8">
<title>Harborline Lending Centres – North Vancouver Mortgage Broker</title>
<link href="https://fonts.googleapis.com/css2?family=Lora:wght@400;700&family=Open+Sans:wght@400;600;700&display=swap" rel="stylesheet">
<style>
:root{
  --navy:#0b3a82;
  --navy-dark:#082c66;
  --gold:#f2c12e;
  --ink:#1d1d1d;
  --body:#6b6b6b;
  --line:#d9d9d9;
  --pale:#eef4fa;
  --white:#ffffff;
}
*{margin:0;padding:0;box-sizing:border-box}
html,body{width:1200px;height:2695px;overflow:hidden}
body{position:relative;background:var(--white);font-family:"Open Sans",Arial,sans-serif;color:var(--ink)}
.abs{position:absolute}
.serif{font-family:"Lora",Georgia,serif}

/* header */
.site-header{left:0;top:0;width:1200px;height:95px;background:var(--navy)}
.brand{left:99px;top:22px;display:flex;align-items:center;gap:12px;color:var(--white);font-family:"Lora",Georgia,serif;font-weight:700;font-size:20px;line-height:1.1}
.brand-mark{width:34px;height:34px;background:var(--gold)}
.nav a{position:absolute;top:36px;color:var(--white);font-size:16px;font-weight:600;text-decoration:none;letter-spacing:.3px}
.nav a.active{color:var(--gold)}

/* hero */
.hero{left:0;top:95px;width:1200px;height:435px;background:linear-gradient(160deg,#6e6a63 0%,#4a4640 40%,#2f3b45 75%,#283847 100%)}
.hero-title{left:0;top:176px;width:1200px;text-align:center;color:var(--white);font-family:"Lora",Georgia,serif;font-weight:700;font-size:46px;letter-spacing:.5px}
.hero-sub{left:0;top:240px;width:1200px;text-align:center;color:var(--white);font-size:22px}
.btn{display:flex;align-items:center;justify-content:center;font-weight:700;text-transform:uppercase;font-size:16px;border-radius:4px}
.btn-gold{background:var(--gold);color:var(--white)}
.btn-ghost{border:2px solid var(--white);color:var(--white)}
.play{left:569px;top:413px;width:62px;height:62px;border:3px solid var(--white);border-radius:50%;background:rgba(0,0,0,.25)}

/* partners */
.partners{left:0;top:530px;width:1200px;height:278px;background:var(--pale)}
.section-title{left:0;width:1200px;text-align:center;font-family:"Lora",Georgia,serif;font-weight:700;font-size:27px;color:var(--ink);letter-spacing:.5px}
.partner-card{top:661px;width:183px;height:83px;background:var(--white);border:3px solid #e2e8ef;display:flex;align-items:center;justify-content:center}
.partner-badge{width:110px;height:34px;border-radius:4px}
.arrow-btn{top:682px;width:42px;height:42px;border:2px solid var(--line);border-radius:50%;background:var(--white)}

/* help */
.help-card{top:1029px;width:308px;height:262px;border:2px solid var(--line);background:var(--white)}
.help-icon{top:975px;width:128px;height:128px;border:2px solid var(--line);border-radius:50%;background:var(--white);display:flex;align-items:center;justify-content:center}
.help-title{top:1134px;width:308px;text-align:center;font-family:"Lora",Georgia,serif;font-weight:700;font-size:20px}
.help-text{top:1180px;width:308px;padding:0 22px;text-align:center;font-size:12.5px;line-height:25px;color:var(--body)}
.help-btn{top:1275px;width:140px;height:38px;font-size:14px}

/* search band */
.search-band{left:0;top:1420px;width:1200px;height:261px;background:linear-gradient(100deg,#b7a59a 0%,#8f8077 35%,#5f6a78 70%,#49556a 100%)}
.search-title{left:0;top:1482px;width:1200px;text-align:center;color:var(--white);font-family:"Lora",Georgia,serif;font-weight:700;font-size:30px}
.search-input{left:260px;top:1564px;width:525px;height:49px;background:var(--white);border-radius:2px;display:flex;align-items:center;gap:14px;padding-left:22px;color:#999;font-size:13px}
.search-btn{left:797px;top:1564px;width:141px;height:49px;font-size:15px}

/* broker */
.broker-photo{left:99px;top:1787px;width:386px;height:433px;background:linear-gradient(160deg,#5a5e63 0%,#3f4247 55%,#26282c 100%)}
.broker-title{left:541px;top:1776px;width:560px;font-family:"Lora",Georgia,serif;font-weight:700;font-size:30px;line-height:42px;color:var(--ink)}
.broker-copy{left:541px;top:1884px;width:560px;font-size:12.3px;line-height:24px;color:var(--body)}
.broker-copy p{margin-bottom:25px}
.app-btn{left:542px;top:2170px;width:279px;height:45px;font-size:14px}
.social{width:42px;height:42px;border:2px solid var(--line);border-radius:50%}

/* footer */
.footer-rule{left:0;top:2318px;width:1200px;height:4px;background:var(--navy)}
.footer-brand{left:104px;top:2371px;width:210px;height:108px;display:flex;align-items:center;gap:10px;font-family:"Lora",Georgia,serif;font-weight:700;font-size:19px;color:var(--ink);line-height:1.15}
.footer-brand .brand-mark{background:var(--navy);width:30px;height:30px;flex:none}
.footer-badge{left:160px;top:2486px;width:86px;height:86px;border-radius:50%;background:var(--navy)}
.footer-head{top:2397px;font-family:"Lora",Georgia,serif;font-weight:700;font-size:17px;color:var(--ink);letter-spacing:.3px}
.footer-links a{position:absolute;left:381px;font-size:12.5px;color:#444;text-decoration:none}
.footer-note{left:586px;top:2443px;width:260px;font-size:12.5px;line-height:22px;color:#444}
.footer-email{left:586px;top:2505px;width:255px;height:32px;border-bottom:1px solid var(--line);font-size:11.5px;color:#aaa;padding:8px 0 0 6px}
.footer-sub{left:586px;top:2545px;width:95px;height:31px;font-size:11.5px}
.contact-item{left:914px;display:flex;gap:14px;font-size:12.5px;line-height:20px;color:#444}
.contact-item svg{flex:none;margin-top:2px}
.footer-divider{left:99px;top:2613px;width:1002px;height:1px;background:var(--line)}
.copyright{left:99px;top:2645px;font-size:12px;color:#555}
.social-sm{top:2642px;width:28px;height:28px;border:1.5px solid #bfc7d3;border-radius:50%}
</style>
</head>
<body>

<header class="abs site-header">
  <div class="abs brand"><span class="brand-mark"></span><span>Harborline Lending<br>Centres</span></div>
  <nav class="nav">
    <a class="active" style="left:580px">HOME</a>
    <a style="left:699px">ABOUT</a>
    <a style="left:825px">BLOG</a>
    <a style="left:939px">CONTACT</a>
  </nav>
  <svg class="abs" style="left:1087px;top:38px" width="18" height="18" viewBox="0 0 18 18"><circle cx="7.5" cy="7.5" r="5.5" fill="none" stroke="#fff" stroke-width="2.4"/><line x1="11.5" y1="11.5" x2="16.5" y2="16.5" stroke="#fff" stroke-width="2.6" stroke-linecap="round"/></svg>
</header>

<section class="abs hero" role="img" aria-label="Aerial photograph of a waterfront city skyline with a bridge and marina"></section>
<h1 class="abs hero-title">HARBORLINE LENDING CENTRES</h1>
<p class="abs hero-sub">Mortgage Specialist in North Vancouver, BC Canada</p>
<a class="abs btn btn-gold" style="left:386px;top:300px;width:205px;height:47px">Get Hooked Up</a>
<a class="abs btn btn-ghost" style="left:609px;top:300px;width:205px;height:47px">I'm a Client</a>
<div class="abs play"><svg width="56" height="56" viewBox="0 0 56 56"><polygon points="22,17 22,39 40,28" fill="#fff"/></svg></div>

<section class="abs partners"></section>
<h2 class="abs section-title" style="top:592px">MY LENDING PARTNERS</h2>
<div class="abs arrow-btn" style="left:38px"><svg width="38" height="38" viewBox="0 0 38 38"><polyline points="21,13 15,19 21,25" fill="none" stroke="#aab" stroke-width="2"/></svg></div>
<div class="abs partner-card" style="left:99px"><span class="partner-badge" style="background:#dfe6d9"></span></div>
<div class="abs partner-card" style="left:304px"><span class="partner-badge" style="background:#d8ecd9"></span></div>
<div class="abs partner-card" style="left:509px"><span class="partner-badge" style="background:#f6e2d0"></span></div>
<div class="abs partner-card" style="left:714px"><span class="partner-badge" style="background:#d6e2ef"></span></div>
<div class="abs partner-card" style="left:919px"><span class="partner-badge" style="background:#d9deea"></span></div>
<div class="abs arrow-btn" style="left:1114px"><svg width="38" height="38" viewBox="0 0 38 38"><polyline points="17,13 23,19 17,25" fill="none" stroke="#aab" stroke-width="2"/></svg></div>

<h2 class="abs section-title" style="top:875px">I NEED HELP WITH</h2>

<div class="abs help-card" style="left:99px"></div>
<div class="abs help-icon" style="left:189px"><svg width="60" height="54" viewBox="0 0 60 54"><polygon points="30,4 4,28 11,28 11,50 25,50 25,36 35,36 35,50 49,50 49,28 56,28" fill="#0b3a82"/></svg></div>
<h3 class="abs help-title" style="left:99px">Home Purchase</h3>
<p class="abs help-text" style="left:99px">Purchasing a home can be a daunting task as the market continues to sizzle and its essential you have a plan in place to avoid confusion.</p>
<a class="abs btn btn-gold help-btn" style="left:183px">Apply Now</a>

<div class="abs help-card" style="left:445px"></div>
<div class="abs help-icon" style="left:535px"><svg width="62" height="62" viewBox="0 0 62 62"><path d="M31 6 A25 25 0 1 0 56 31" fill="none" stroke="#0b3a82" stroke-width="3.5"/><circle cx="52" cy="19" r="2.5" fill="#0b3a82"/><circle cx="45" cy="11" r="2.5" fill="#0b3a82"/><text x="31" y="41" text-anchor="middle" font-family="Open Sans,Arial,sans-serif" font-weight="700" font-size="28" fill="#0b3a82">$</text></svg></div>
<h3 class="abs help-title" style="left:445px">Refinance</h3>
<p class="abs help-text" style="left:445px">Purchasing a home can be a daunting task as the market continues to sizzle and its essential you have a plan in place to avoid confusion.</p>
<a class="abs btn btn-gold help-btn" style="left:529px">Apply Now</a>

<div class="abs help-card" style="left:792px"></div>
<div class="abs help-icon" style="left:882px"><svg width="60" height="60" viewBox="0 0 60 60"><path d="M10 27 A20 20 0 0 1 46 16" fill="none" stroke="#0b3a82" stroke-width="6"/><polygon points="50,6 52,24 35,21" fill="#0b3a82"/><path d="M50 33 A20 20 0 0 1 14 44" fill="none" stroke="#0b3a82" stroke-width="6"/><polygon points="10,54 8,36 25,39" fill="#0b3a82"/></svg></div>
<h3 class="abs help-title" style="left:792px">Renewal</h3>
<p class="abs help-text" style="left:792px">Purchasing a home can be a daunting task as the market continues to sizzle and its essential you have a plan in place to avoid confusion.</p>
<a class="abs btn btn-gold help-btn" style="left:876px">Apply Now</a>

<section class="abs search-band" role="img" aria-label="Close-up photograph of hands typing on a laptop keyboard"></section>
<h2 class="abs search-title">MORTGAGE OR REAL ESTATE QUESTIONS?</h2>
<div class="abs search-input"><svg width="15" height="15" viewBox="0 0 18 18"><circle cx="7.5" cy="7.5" r="5.5" fill="none" stroke="#555" stroke-width="2.4"/><line x1="11.5" y1="11.5" x2="16.5" y2="16.5" stroke="#555" stroke-width="2.6" stroke-linecap="round"/></svg>Search our data base</div>
<a class="abs btn btn-gold search-btn">Search</a>

<div class="abs broker-photo" role="img" aria-label="Portrait photograph of the mortgage broker in a dark suit"></div>
<h2 class="abs broker-title">NORTH VANCOUVER MORTGAGE<br>BROKER</h2>
<div class="abs broker-copy">
  <p>Purchasing a home, refinancing a mortgage and renewing a mortgage have one thing in common: they can represent an exciting time in an individual's life but they can also be complex.</p>
  <p>I am dedicated to giving back to the region by helping people save thousands of dollars in interest and prepayment expenses and find solutions that are fitted to your specific situation.</p>
  <p>In addition to getting you a fantastic rate, I ensure that I take enough time for each and every one of my clients to go over every detail in order to see that their mortgage repayment schedule is on track with their financial objectives. It is my mission to help people in this wonderful area get the best North Vancouver mortgage package possible while providing tremendous care and service.</p>
</div>
<a class="abs btn btn-gold app-btn">Download My Mortgage App</a>
<span class="abs social" style="left:842px;top:2172px"></span>
<span class="abs social" style="left:891px;top:2172px"></span>
<span class="abs social" style="left:940px;top:2172px"></span>
<span class="abs social" style="left:989px;top:2172px"></span>
<span class="abs social" style="left:1038px;top:2172px"></span>

<div class="abs footer-rule"></div>
<div class="abs footer-brand"><span class="brand-mark"></span><span>Harborline Lending Centres</span></div>
<div class="abs footer-badge"></div>

<h4 class="abs footer-head" style="left:381px">INFORMATION</h4>
<nav class="footer-links">
  <a style="top:2443px">Home</a>
  <a style="top:2473px">About</a>
  <a style="top:2504px">Blog</a>
  <a style="top:2534px">Contact</a>
</nav>

<h4 class="abs footer-head" style="left:586px">NEWSLETTER SUBSCRIPTION</h4>
<p class="abs footer-note">Register your Email Address to get Information about us</p>
<div class="abs footer-email">Email Address</div>
<a class="abs btn btn-gold footer-sub">Subscribe</a>

<h4 class="abs footer-head" style="left:914px">CONTACT US</h4>
<div class="abs contact-item" style="top:2443px"><svg width="12" height="16" viewBox="0 0 12 16"><path d="M6 0C2.7 0 0 2.6 0 5.8 0 10 6 16 6 16s6-6 6-10.2C12 2.6 9.3 0 6 0zm0 8a2.2 2.2 0 1 1 0-4.4A2.2 2.2 0 0 1 6 8z" fill="#0b3a82"/></svg><span>418 Harbourview Rd.<br>North Vancouver, BC V7L 3K5</span></div>
<div class="abs contact-item" style="top:2496px"><svg width="14" height="14" viewBox="0 0 14 14"><path d="M3 0l3 3-2 2c1 2 3 4 5 5l2-2 3 3-2 3C6 14 0 8 0 3z" fill="#0b3a82"/></svg><span>778.555.0142</span></div>
<div class="abs contact-item" style="top:2529px"><svg width="14" height="14" viewBox="0 0 14 14"><rect x="0" y="4" width="14" height="8" rx="1" fill="#0b3a82"/><rect x="3" y="0" width="8" height="5" fill="#0b3a82"/><rect x="3" y="9" width="8" height="5" fill="#fff" stroke="#0b3a82"/></svg><span>604.555.0187</span></div>
<div class="abs contact-item" style="top:2561px"><svg width="15" height="12" viewBox="0 0 15 12"><rect width="15" height="12" rx="1" fill="#0b3a82"/><polyline points="1,1.5 7.5,7 14,1.5" fill="none" stroke="#fff" stroke-width="1.3"/></svg><span>colin@shorelinehomeloans.ca</span></div>

<div class="abs footer-divider"></div>
<p class="abs copyright">Copyrights © 2017, Harborline Lending Centres. All rights reserved.</p>
<span class="abs social-sm" style="left:975px"></span>
<span class="abs social-sm" style="left:1008px"></span>
<span class="abs social-sm" style="left:1041px"></span>
<span class="abs social-sm" style="left:1074px"></span>

</body>
</html>
```